Harborlane Products Flyer

Harborlane Lending Group, Inc.
Licensed Mortgage Company
Serving the DMV since 1997
"You open the Harborlane, we'll carry the load"
We specialize in...
FHA Loans
* Credit Scores as low as 500
* 203K Renovation Loans
Conventional Loans
* As little as 1% Down
* Bank Statement for Self-Employed
Investor Loans
* DSCR, & Fix & Flip
* Commercial & New Construction
Other Programs
* HELOCS & Reverse Mortgages
Call today for a free consultation
(800) 914-6027
www.harborlanehomeloans.com
NMLS #731860

```html
<!DOCTYPE html>
<html lang="en">
<head>
<meta charset="utf-8">
<title>Harborlane Products Flyer</title>
<link rel="stylesheet" href="https://fonts.googleapis.com/css2?family=Bebas+Neue&family=Poppins:wght@400;600;700&display=swap">
<style>
  :root {
    --navy: #0f4d6e;
    --gold: #bfae44;
    --white: #ffffff;
    --ink: #16232b;
    --backdrop: #e7e7e7;
    --photo-a: #e9e2d8;
    --photo-b: #b58a6a;
  }
  * { box-sizing: border-box; margin: 0; padding: 0; }
  html, body { width: 1200px; height: 865px; overflow: hidden; background: var(--backdrop); }
  body { font-family: "Poppins", sans-serif; color: var(--ink); position: relative; }

  .flyer {
    position: absolute; left: 280px; top: 18px;
    width: 640px; height: 828px; background: var(--white);
    overflow: hidden; box-shadow: 0 6px 24px rgba(0,0,0,.18);
  }

  .brand { position: absolute; left: 30px; top: 34px; display: flex; align-items: center; gap: 10px; }
  .brand-dot { width: 34px; height: 34px; border-radius: 50%; background: var(--navy); flex: none; }
  .brand-name { font-weight: 700; font-size: 17px; line-height: 1.15; color: var(--navy); }

  .nmls {
    position: absolute; right: 44px; top: 40px;
    background: var(--navy); color: var(--white);
    font-size: 17px; padding: 10px 14px; letter-spacing: .3px;
  }
  .serving {
    position: absolute; right: 56px; top: 96px; text-align: center;
    font-weight: 700; font-size: 13px; line-height: 1.2; color: var(--navy);
  }
  .serving span { color: var(--gold); display: block; }

  .photo {
    position: absolute; left: 0; top: 150px; width: 640px; height: 300px;
    background: linear-gradient(135deg, var(--photo-a) 0%, var(--photo-b) 55%, var(--photo-a) 100%);
  }
  .photo-rule { position: absolute; left: 0; top: 450px; width: 460px; height: 10px; background: var(--navy); }

  .programs { position: absolute; right: 16px; top: 168px; width: 190px; }
  .program {
    height: 140px; padding: 12px 10px 0; text-align: center; color: var(--white);
    display: flex; flex-direction: column; align-items: center;
  }
  .program.navy { background: var(--navy); }
  .program.gold { background: var(--gold); }
  .program-icon {
    width: 38px; height: 38px; border-radius: 50%;
    display: flex; align-items: center; justify-content: center; margin-bottom: 8px;
  }
  .navy .program-icon { background: var(--gold); }
  .gold .program-icon { background: var(--navy); }
  .program-title { font-weight: 700; font-size: 14px; margin-bottom: 3px; }
  .program-detail { font-size: 11px; line-height: 1.3; }

  .headline { position: absolute; left: 32px; top: 474px; font-family: "Bebas Neue", sans-serif; font-weight: 400; line-height: .9; }
  .headline .lead { font-size: 56px; color: var(--navy); display: block; }
  .headline .name { font-size: 78px; color: var(--gold); display: block; }
  .headline .close { font-size: 34px; color: var(--navy); display: block; margin-top: 4px; }

  .call {
    position: absolute; left: 22px; top: 636px; width: 210px;
    background: var(--navy); color: var(--white); padding: 8px 14px;
    font-size: 12px; line-height: 1.25;
  }
  .call strong { font-size: 15px; display: block; }
  .call-phone {
    position: absolute; left: 34px; top: 702px; display: flex; align-items: center; gap: 10px;
    font-weight: 700; font-size: 21px; line-height: 1.2; color: var(--ink);
  }

  .footer {
    position: absolute; left: 0; bottom: 0; width: 640px; height: 74px;
    background: var(--navy); border-top: 4px solid var(--gold);
    display: flex; align-items: center; justify-content: space-between; padding: 0 26px;
    color: var(--white); font-size: 9.5px; line-height: 1.3;
  }
  .footer-item { display: flex; align-items: center; gap: 8px; }
  .footer-icon {
    width: 20px; height: 20px; border-radius: 50%; background: var(--gold);
    display: flex; align-items: center; justify-content: center; flex: none;
  }
</style>
</head>
<body>
  <article class="flyer">
    <header>
      <div class="brand">
        <span class="brand-dot"></span>
        <span class="brand-name">Harborlane Lending<br>Group, Inc.</span>
      </div>
      <div class="nmls">NMLS #731860</div>
      <p class="serving">Serving the DMV <span>Since 1997</span></p>
    </header>

    <div class="photo" role="img" aria-label="Photo of a smiling family of four relaxing together on a white bed"></div>
    <div class="photo-rule"></div>

    <section class="programs">
      <div class="program navy">
        <div class="program-icon"><svg width="20" height="20" viewBox="0 0 20 20" fill="none" stroke="#fff" stroke-width="1.6"><path d="M3 10 10 4l7 6M5 9v7h10V9"/></svg></div>
        <p class="program-title">FHA Loans</p>
        <p class="program-detail">Credit Scores as low as 500<br>203K Renovation Loans</p>
      </div>
      <div class="program gold">
        <div class="program-icon"><svg width="20" height="20" viewBox="0 0 20 20" fill="none" stroke="#fff" stroke-width="1.6"><rect x="5" y="3" width="10" height="14"/><path d="M8 7h4M8 10h4M8 13h2"/></svg></div>
        <p class="program-title">Conventional Loans</p>
        <p class="program-detail">As little as 1% Down<br>Bank Statement for Self Employed</p>
      </div>
      <div class="program navy">
        <div class="program-icon"><svg width="20" height="20" viewBox="0 0 20 20" fill="none" stroke="#fff" stroke-width="1.6"><circle cx="10" cy="7" r="3"/><path d="M4 17c0-3.5 2.7-5.5 6-5.5s6 2 6 5.5"/></svg></div>
        <p class="program-title">Investor Loans</p>
        <p class="program-detail">DSCR, &amp; Fix &amp; Flip<br>Commercial &amp; New Construction</p>
      </div>
      <div class="program gold">
        <div class="program-icon"><svg width="20" height="20" viewBox="0 0 20 20" fill="none" stroke="#fff" stroke-width="1.6"><rect x="3" y="4" width="14" height="10"/><path d="M6 8h8M6 11h5"/></svg></div>
        <p class="program-title">Other Programs</p>
        <p class="program-detail">HELOCS &amp; Reverse<br>Mortgages</p>
      </div>
    </section>

    <h1 class="headline">
      <span class="lead">You open the</span>
      <span class="name">Harborlane</span>
      <span class="close">We'll carry the load</span>
    </h1>

    <div class="call"><strong>Call Today</strong>for a Free Consultation</div>
    <div class="call-phone">
      <svg width="18" height="18" viewBox="0 0 24 24" fill="#bfae44"><path d="M6.6 10.8a15 15 0 0 0 6.6 6.6l2.2-2.2c.3-.3.7-.4 1-.2 1.1.4 2.3.6 3.6.6.6 0 1 .4 1 1V20c0 .6-.4 1-1 1A17 17 0 0 1 3 4c0-.6.4-1 1-1h3.5c.6 0 1 .4 1 1 0 1.3.2 2.5.6 3.6.1.3 0 .7-.2 1z"/></svg>
      (800) 914-6027
    </div>

    <footer class="footer">
      <div class="footer-item">
        <span class="footer-icon"><svg width="10" height="12" viewBox="0 0 10 12" fill="#0f4d6e"><path d="M5 0a4 4 0 0 0-4 4c0 3 4 8 4 8s4-5 4-8a4 4 0 0 0-4-4zm0 5.5A1.5 1.5 0 1 1 5 2.5a1.5 1.5 0 0 1 0 3z"/></svg></span>
        <span>MARYLAND OFFICE: 2417<br>Marlow Ridge Rd, Columbia, MD 21044</span>
      </div>
      <div class="footer-item">
        <span class="footer-icon"><svg width="12" height="12" viewBox="0 0 12 12" fill="none" stroke="#0f4d6e" stroke-width="1.2"><circle cx="6" cy="6" r="5"/><path d="M1 6h10M6 1c2 2 2 8 0 10M6 1c-2 2-2 8 0 10"/></svg></span>
        <span>www.harborlanehomeloans.com</span>
      </div>
      <div class="footer-item">
        <span class="footer-icon"><svg width="11" height="11" viewBox="0 0 24 24" fill="#0f4d6e"><path d="M6.6 10.8a15 15 0 0 0 6.6 6.6l2.2-2.2c.3-.3.7-.4 1-.2 1.1.4 2.3.6 3.6.6.6 0 1 .4 1 1V20c0 .6-.4 1-1 1A17 17 0 0 1 3 4c0-.6.4-1 1-1h3.5c.6 0 1 .4 1 1 0 1.3.2 2.5.6 3.6.1.3 0 .7-.2 1z"/></svg></span>
        <span>(800) 914-6027</span>
      </div>
    </footer>
  </article>
</body>
</html>
```